I am looking for a flyer design for my upcoming symposium. Here are the details for the flyer and pictures of speakers are attached.

Name of Symposium: Layered and Regional Proteomics Colloquium, Sponsored by the Dorwick Chromatin Institute and the Department of Bioengineering
Date: January 8, 2018
Location: Halvorsen Auditorium, Brantley Center for Applied Discovery, 2175 Marlowe Crest Ave, Philadelphia, PA 19139

Reception to follow after the symposium.

Also, please add - Register and upload abstracts for the symposium at www.qelvarn.example. Registration and abstract submission closes on January 4, 2018.

Keynote Speaker:
Greta Lindqvar, Ph.D.
NVOS Director General; Professor, Ostrel Academy; Director, Genetics and Developmental Biology at Institut Varanne
Ostrel Academy, NVOS, Institut Varanne
"Title of talk TBA."

Speakers:
Rina Fostwell, Ph.D.
Assistant Professor of Cell and Developmental Biology
Dunmore State University, TKHV
"Title of talk TBA."

Owen Trask, Ph.D.
Assistant Professor of Genetics
"Title of talk TBA."

Lia Vestur, Ph.D.
Professor, Grauwald University
Otto Ferlsang Center for Molecular Medicine
"Title of talk TBA."

Hao Lin, Ph.D.
Professor of Cellular and Molecular Medicine
Coastal Meridian University
"Title of talk TBA."

Jun Zhao, Ph.D.
Associate Professor of Pediatrics
The Riverbend Youth Medical Center
"Spatial genome re-organization between fetal and adult hematopoietic stem cells."

Mei Sun, Ph.D.
Professor, Department of Genetics
Pellridge Medical School
"Title of talk TBA."

```html
<!DOCTYPE html>
<html lang="en">
<head>
<meta charset="utf-8">
<title>Layered and Regional Proteomics Colloquium</title>
<link rel="stylesheet" href="https://fonts.googleapis.com/css2?family=Montserrat:wght@300;400;500;600;700;800&display=swap">
<style>
  :root {
    --maroon: #5c0a10;
    --red-glow: #c4141f;
    --red-rule: #b8141c;
    --slate: #2b2d30;
    --slate-dark: #1e2022;
    --gold: #f5d547;
    --sky: #8fd3f0;
    --white: #ffffff;
    --navy: #1c3b58;
    --paper: #ffffff;
  }
  * { margin: 0; padding: 0; box-sizing: border-box; }
  html, body { width: 927px; height: 1200px; overflow: hidden; background: var(--paper); }
  body { font-family: "Montserrat", Arial, sans-serif; position: relative; }

  .flyer { position: relative; width: 927px; height: 1200px; background: var(--paper); }

  .title-panel {
    position: absolute; left: 14px; top: 12px; width: 436px; height: 940px;
    background: var(--maroon);
    overflow: hidden;
  }
  .helix-art {
    position: absolute; left: 0; top: 350px; width: 436px; height: 590px;
    background:
      radial-gradient(ellipse 45% 60% at 45% 55%, var(--red-glow) 0%, rgba(196,20,31,0.55) 45%, rgba(92,10,16,0) 80%),
      linear-gradient(180deg, var(--maroon) 0%, #8e1018 45%, #a3121b 75%, #7a0c13 100%);
  }
  .event-title {
    position: absolute; left: 0; top: 42px; width: 436px; text-align: center;
    color: var(--gold); font-weight: 800; font-size: 48px; line-height: 64px; letter-spacing: 0.5px;
  }
  .event-kind {
    position: absolute; left: 0; top: 234px; width: 436px; text-align: center;
    color: var(--white); font-weight: 400; font-size: 47px; letter-spacing: 1px;
  }
  .sponsor-line {
    position: absolute; left: 0; top: 303px; width: 436px; text-align: center;
    color: var(--white); font-size: 16.5px; line-height: 22px; font-weight: 400;
  }

  .divider { position: absolute; left: 450px; top: 12px; width: 3px; height: 940px; background: var(--red-rule); }
  .base-rule { position: absolute; left: 14px; top: 950px; width: 901px; height: 3px; background: var(--red-rule); }

  .speaker-panel {
    position: absolute; left: 453px; top: 12px; width: 462px; height: 938px;
    background: linear-gradient(160deg, var(--slate) 0%, var(--slate-dark) 100%);
  }
  .section-head {
    position: absolute; display: flex; align-items: center; gap: 10px;
    font-weight: 700; font-size: 16px; left: 160px; right: 0;
  }
  .section-head::after { content: ""; flex: 1; height: 2px; background: currentColor; }
  .section-head.keynote { top: 40px; color: var(--gold); }
  .section-head.speakers { top: 239px; left: 156px; color: var(--sky); }

  .portrait {
    position: absolute; border-radius: 50%; border: 3px solid var(--white);
    background: radial-gradient(circle at 50% 40%, #c9a58c 0%, #7a5a48 55%, #3d3532 100%);
  }
  .portrait.keynote-photo { left: 37px; top: 84px; width: 112px; height: 112px; }
  .portrait.speaker-photo { width: 88px; height: 88px; left: 54px; }

  .bio { position: absolute; left: 154px; font-size: 12.8px; line-height: 16px; font-weight: 400; }
  .bio .name { font-weight: 700; font-size: 13.5px; display: block; margin-bottom: 1px; }
  .bio.keynote-bio { top: 97px; color: var(--gold); }
  .bio.speaker-bio { color: var(--sky); }

  .org-mark {
    position: absolute; left: 38px; width: 200px;
    display: flex; align-items: center; gap: 10px;
    font-weight: 600; font-size: 16px; line-height: 20px; color: var(--navy);
  }
  .org-mark .dot { flex: none; width: 32px; height: 32px; border-radius: 50%; background: var(--navy); }
  .org-mark.engineering { top: 1020px; }
  .org-mark.institute { top: 1110px; }
  .org-mark.institute .dot { border-radius: 0; }

  .event-info { position: absolute; right: 34px; top: 990px; text-align: right; color: var(--navy); }
  .event-date { font-size: 31px; font-weight: 700; letter-spacing: 0.3px; margin-bottom: 12px; }
  .venue { font-size: 14px; line-height: 17px; margin-bottom: 24px; }
  .register { font-size: 16.3px; line-height: 21px; margin-bottom: 12px; }
  .register strong { font-weight: 700; }
  .reception { font-size: 16.3px; }
</style>
</head>
<body>
<main class="flyer">
  <section class="title-panel">
    <div class="helix-art" role="img" aria-label="Glowing red DNA double helix on a deep red background"></div>
    <h1 class="event-title">LAYERED AND<br>REGIONAL<br>PROTEOMICS</h1>
    <div class="event-kind">COLLOQUIUM</div>
    <p class="sponsor-line">Sponsored by the Dorwick Chromatin Institute<br>and the Department of Bioengineering</p>
  </section>

  <div class="divider"></div>

  <section class="speaker-panel">
    <h2 class="section-head keynote">Keynote Speaker</h2>
    <div class="portrait keynote-photo" role="img" aria-label="Portrait of Greta Lindqvar"></div>
    <p class="bio keynote-bio"><span class="name">Greta Lindqvar, Ph.D.</span>NVOS Director General; Professor,<br>Ostrel Academy; Director, Genetics and<br>Developmental Biology at Institut Varanne<br>Ostrel Academy, NVOS, Institut Varanne<br>"Title of talk TBA."</p>

    <h2 class="section-head speakers">Speakers</h2>

    <div class="portrait speaker-photo" style="top:284px" role="img" aria-label="Portrait of Rina Fostwell"></div>
    <p class="bio speaker-bio" style="top:293px"><span class="name">Rina Fostwell, Ph.D.</span>Assistant Professor of Cell and<br>Developmental Biology<br>Dunmore State University, TKHV<br>"Title of talk TBA."</p>

    <div class="portrait speaker-photo" style="top:389px" role="img" aria-label="Portrait of Owen Trask"></div>
    <p class="bio speaker-bio" style="top:399px"><span class="name">Owen Trask, Ph.D.</span>Assistant Professor of Genetics<br>Dunmore State University, TKHV<br>"Title of talk TBA."</p>

    <div class="portrait speaker-photo" style="top:495px" role="img" aria-label="Portrait of Lia Vestur"></div>
    <p class="bio speaker-bio" style="top:500px"><span class="name">Lia Vestur, Ph.D.</span>Professor, Grauwald University<br>Otto Ferlsang Center for<br>Molecular Medicine | "Title of talk TBA."</p>

    <div class="portrait speaker-photo" style="top:601px" role="img" aria-label="Portrait of Hao Lin"></div>
    <p class="bio speaker-bio" style="top:600px"><span class="name">Hao Lin, Ph.D.</span>Professor of Cellular and<br>Molecular Medicine<br>Coastal Meridian University<br>"Title of talk TBA."</p>

    <div class="portrait speaker-photo" style="top:720px" role="img" aria-label="Portrait of Jun Zhao"></div>
    <p class="bio speaker-bio" style="top:720px"><span class="name">Jun Zhao, Ph.D.</span>Associate Professor of Pediatrics<br>The Riverbend Youth Medical Center<br>"Spatial genome re-organization<br>between fetal and adult<br>hematopoietic stem cells."</p>

    <div class="portrait speaker-photo" style="top:831px" role="img" aria-label="Portrait of Mei Sun"></div>
    <p class="bio speaker-bio" style="top:857px"><span class="name">Mei Sun, Ph.D.</span>Professor, Department of Genetics<br>Pellridge Medical School | "Title of talk TBA."</p>
  </section>

  <div class="base-rule"></div>

  <div class="org-mark engineering"><span class="dot"></span><span>Halden<br>Engineering</span></div>
  <div class="org-mark institute"><span class="dot"></span><span>Dorwick Chromatin<br>Institute</span></div>

  <section class="event-info">
    <div class="event-date">January 8, 2018</div>
    <p class="venue">Halvorsen Auditorium, Brantley Center for Applied<br>Discovery, 2175 Marlowe Crest Ave, Philadelphia, PA 19139</p>
    <p class="register">Register and upload abstracts for the symposium at www.qelvarn.example.<br>Registration and abstract submission closes on <strong>January 4, 2018.</strong></p>
    <p class="reception">Reception to follow after the symposium.</p>
  </section>
</main>
</body>
</html>
```